Redesign of the UI of a customer service platform

To improve the user experience of our customers, we need a new design for our agent interface of our customer service platform (velorant.com).
The focus will be on the dashboard and the inbox screens (see attached) along with the common UI elements (Buttons, menu, fonts, forms...)
We want a simple and distinctive design

Target Market(s)

Worldwide

Industry/Entity Type

It Service

Number of Pages Required

3 page

Font styles to use
Sans Serif

Requirements
Must have
• New Onboarding page: this is a new page that is shown to user the first time they login to the platform. This will replace the current onboarding screen (setup SMS, Setup widget...etc)
• Dashboard page: to access important information and activate services (see screenshot from current site)
• Inbox page: to manage all the interactions with customers. (see screenshot from current site)
• UI elements (buttons, menus, forms, tables, fonts, color palette)

```html
<!DOCTYPE html>
<html lang="en">
<head>
<meta charset="utf-8">
<title>Velorant — Inbox</title>
<link href="https://fonts.googleapis.com/css2?family=Open+Sans:wght@400;600&display=swap" rel="stylesheet">
<style>
:root{
  --blue:#3a95c4;--cyan:#1fd8ee;--cyan-soft:#dcfbfe;--cyan-line:#a9eff7;
  --yellow:#f9c80e;--green:#23c483;--red:#e8262b;--text:#444;--muted:#888;
  --line:#e3e3e3;--panel:#f5f5f5;--bar:#f0f0f0;--photo:#b98a74;--photo-dark:#5b4a42;
}
*{box-sizing:border-box;margin:0;padding:0}
html,body{width:1200px;height:1014px;overflow:hidden;background:#fff;font-family:"Open Sans",sans-serif;color:var(--text)}
.abs{position:absolute}
.topbar{position:absolute;left:0;top:0;width:1200px;height:62px;border-bottom:1px solid var(--line);background:#fff}
.brand{left:0;top:0;width:86px;height:62px;display:flex;align-items:center;justify-content:center}
.brand span{width:34px;height:34px;border-radius:50%;background:#333}
.nav{left:86px;top:0;display:flex;height:62px}
.nav-item{width:99.5px;height:62px;border-right:1px solid var(--line);position:relative;font-size:10.5px;text-align:center;color:#555;padding-top:38px}
.nav-item svg{position:absolute;left:50%;top:15px;transform:translateX(-50%)}
.nav-item.active{background:#f4f4f4}
.badge{position:absolute;top:25px;width:22px;height:22px;border-radius:50%;color:#fff;font-size:11px;line-height:22px;text-align:center}
.user{left:1044px;top:9px;display:flex;align-items:center;font-size:11px;color:#555}
.avatar{border-radius:50%;background:linear-gradient(160deg,var(--photo),var(--photo-dark))}
.user .avatar{width:46px;height:46px;border:3px solid #c6f4f8;margin-right:9px}
.online{left:1041px;top:11px;width:11px;height:11px;border-radius:50%;background:var(--green)}
.sidebar{left:0;top:62px;width:344px;height:903px;background:var(--panel);border-right:1px solid var(--line)}
.sidebar-head{height:74px;background:var(--blue);color:#fff;text-align:center;padding-top:12px;position:relative}
.sidebar-head h1{font-size:17.5px;font-weight:400;margin-left:-26px}
.sidebar-head p{font-size:12.5px;margin-left:-26px;margin-top:2px}
.sidebar-head svg{position:absolute;right:22px;top:31px}
.conv{height:70px;background:#fff;border-bottom:1px solid var(--line);position:relative}
.conv .avatar{position:absolute;left:17px;top:12px;width:47px;height:47px;border:2px solid #e5e5e5}
.conv .name{position:absolute;left:75px;top:14px;font-size:14px;color:#333}
.conv .snippet{position:absolute;left:75px;top:42px;font-size:11.5px;color:var(--muted);display:flex;align-items:center;gap:4px}
.conv .time{position:absolute;right:15px;top:12px;font-size:10.5px;color:var(--red)}
.conv .mini{position:absolute;top:32px;width:24px;height:24px;border:2px solid #ddd}
.dot-src{width:9px;height:9px;border-radius:50%;background:var(--cyan);display:inline-block}
.profile{left:344px;top:62px;width:437px;height:903px;border-right:1px solid var(--line);background:#fff}
.btn{position:absolute;top:19px;height:28px;color:#fff;font-size:12.5px;display:flex;align-items:center;justify-content:center;gap:5px;border-radius:1px}
.big-photo{left:108px;top:73px;width:194px;height:194px;border-radius:50%;background:#eee;display:flex;align-items:center;justify-content:center}
.big-photo div{width:176px;height:176px;border-radius:50%;background:linear-gradient(160deg,#c48a72,#8a3d32)}
.meta{left:316px;top:154px;font-size:12.5px;color:#555;line-height:27px}
.meta div{display:flex;align-items:center;gap:8px}
.pname{left:0;width:409px;top:280px;text-align:center;font-size:18px;color:var(--blue)}
.bar{position:absolute;left:0;width:436px;height:40px;background:linear-gradient(#fafafa,#eee);border-top:1px solid var(--line);border-bottom:1px solid var(--line);font-size:13.5px;color:#555;padding:0 18px;display:flex;align-items:center;justify-content:space-between}
.bar b{font-weight:400;font-size:13px}
.details{left:0;top:407px;width:436px;font-size:12.5px;color:#555}
.row{position:absolute;left:0;width:436px;height:20px}
.row .k{position:absolute;right:306px;text-align:right;white-space:nowrap}
.row .v{position:absolute;left:151px}
.row svg{position:absolute;left:393px;top:1px}
.show-all{left:175px;top:589px;width:88px;height:26px;background:var(--yellow);color:#fff;font-size:12px;display:flex;align-items:center;justify-content:center;gap:5px}
.task{position:absolute;left:18px;width:410px;font-size:11.5px;color:#555;height:18px}
.task .t{position:absolute;left:20px}
.task .d{position:absolute;left:271px}
.empty{left:0;top:864px;width:436px;text-align:center;font-size:14px;color:#666}
.chat{left:781px;top:62px;width:419px;height:903px;background:#fff}
.chat .avatar{position:absolute;width:68px;height:68px;border:3px solid #bff1f6}
.bubble{position:absolute;background:var(--cyan-soft);border:1px solid var(--cyan-line);font-size:12.5px;color:#555;padding:0 17px;display:flex;align-items:center;line-height:23px}
.input-wrap{left:807px;top:907px;width:364px;height:58px;background:var(--cyan-soft);border:1px solid var(--cyan-line)}
.input-wrap div{position:absolute;left:9px;top:8px;width:345px;height:41px;background:#fff;border:1px solid var(--cyan-line);font-size:13px;color:#555;padding-left:16px;line-height:39px}
.footer{left:0;top:984px;width:1200px;height:30px;background:#f5f5f5;border-top:1px solid var(--line);font-size:10.5px;color:#555;text-align:center;line-height:30px}
</style>
</head>
<body>
<header class="topbar">
  <div class="abs brand"><span></span></div>
  <nav class="abs nav">
    <div class="nav-item active"><svg width="14" height="12" viewBox="0 0 14 12"><rect x="1" y="1" width="12" height="10" fill="none" stroke="#777"/><path d="M1 1l6 5 6-5" fill="none" stroke="#777"/></svg>INBOX<span class="badge" style="left:69px;background:var(--green)">4</span></div>
    <div class="nav-item"><svg width="12" height="14" viewBox="0 0 12 14"><path d="M1 1h7l3 3v9H1z" fill="none" stroke="#777"/><path d="M3 7h6M3 10h6" stroke="#777"/></svg>TASKS<span class="badge" style="left:72px;background:var(--yellow)">4</span></div>
    <div class="nav-item"><svg width="12" height="13" viewBox="0 0 12 13"><circle cx="6" cy="4" r="3" fill="#777"/><path d="M0 13c0-4 3-5 6-5s6 1 6 5z" fill="#777"/></svg>CUSTOMERS</div>
    <div class="nav-item"><svg width="14" height="14" viewBox="0 0 14 14"><path d="M13 1L1 6l5 2 2 5z" fill="none" stroke="#777"/></svg>CAMPAIGNS</div>
    <div class="nav-item"><svg width="16" height="12" viewBox="0 0 16 12"><rect x="1" y="1" width="14" height="10" fill="none" stroke="#777"/><path d="M1 4h14" stroke="#777" stroke-width="2"/></svg>PAYMENTS</div>
    <div class="nav-item"><svg width="16" height="13" viewBox="0 0 16 13"><path d="M1 0v12h15" fill="none" stroke="#777"/><path d="M4 11V6M7 11V3M10 11V5M13 11V2" stroke="#777" stroke-width="2"/></svg>REPORTS</div>
    <div class="nav-item"><svg width="14" height="14" viewBox="0 0 14 14"><circle cx="7" cy="7" r="5" fill="none" stroke="#777" stroke-width="3" stroke-dasharray="2.5 1.4"/><circle cx="7" cy="7" r="2" fill="#777"/></svg>SETTINGS</div>
  </nav>
  <div class="abs user"><div class="avatar" role="img" aria-label="Agent profile photo"></div>KYLE BRENAN</div>
  <div class="abs online"></div>
</header>

<aside class="abs sidebar">
  <div class="sidebar-head"><h1>Open Conversations</h1><p>New or assigned to me</p>
    <svg width="12" height="8" viewBox="0 0 12 8"><path d="M1 1l5 5 5-5" fill="none" stroke="#fff" stroke-width="1.6"/></svg></div>
  <div class="conv"><div class="avatar" role="img" aria-label="Customer photo"></div><div class="name">Lena Marsh</div><div class="time">2 mins ago</div>
    <div class="avatar mini" style="left:306px" role="img" aria-label="Agent photo"></div>
    <div class="snippet"><svg width="13" height="12" viewBox="0 0 14 14"><path d="M13 1L1 6l5 2 2 5z" fill="none" stroke="var(--cyan)" stroke-width="1.5"/></svg>Yes that would be great, please</div></div>
  <div class="conv"><div class="avatar" role="img" aria-label="Customer photo"></div><div class="name">Owen Tully</div><div class="time">9 mins ago</div>
    <div class="snippet"><svg width="15" height="12" viewBox="0 0 15 12"><rect x="1" y="1" width="13" height="8" fill="none" stroke="var(--cyan)" stroke-width="1.5"/><path d="M5 11h5" stroke="var(--cyan)" stroke-width="1.5"/></svg>Hi, I need to know if there are...</div></div>
  <div class="conv"><div class="avatar" role="img" aria-label="Customer photo"></div><div class="name">Lena Marsh</div><div class="time">2 mins ago</div>
    <div class="avatar mini" style="left:277px" role="img" aria-label="Agent photo"></div><div class="avatar mini" style="left:306px" role="img" aria-label="Agent photo"></div>
    <div class="snippet"><span class="dot-src"></span>The issue occured one more...</div></div>
  <div class="conv"><div class="avatar" role="img" aria-label="Customer photo"></div><div class="name">Owen Tully</div><div class="time">9 mins ago</div>
    <div class="snippet"><svg width="15" height="12" viewBox="0 0 15 12"><rect x="1" y="1" width="13" height="8" fill="none" stroke="var(--cyan)" stroke-width="1.5"/><path d="M5 11h5" stroke="var(--cyan)" stroke-width="1.5"/></svg>Hi, I need to know if there are...</div></div>
</aside>

<main class="abs profile">
  <div class="btn" style="left:212px;width:77px;background:var(--cyan)"><svg width="11" height="9" viewBox="0 0 11 9"><path d="M1 4l3 3 6-6" fill="none" stroke="#fff" stroke-width="2"/></svg>Close</div>
  <div class="btn" style="left:298px;width:77px;background:var(--yellow)"><svg width="12" height="10" viewBox="0 0 12 10"><path d="M7 0l5 4-5 4V5C3 5 1 7 0 10 0 5 3 3 7 3z" fill="#fff"/></svg>Transfer</div>
  <svg class="abs" style="left:389px;top:26px" width="4" height="16" viewBox="0 0 4 16"><circle cx="2" cy="2" r="1.7" fill="#555"/><circle cx="2" cy="8" r="1.7" fill="#555"/><circle cx="2" cy="14" r="1.7" fill="#555"/></svg>
  <div class="abs big-photo"><div role="img" aria-label="Customer profile photo"></div></div>
  <div class="abs meta">
    <div><svg width="13" height="12" viewBox="0 0 14 14"><path d="M13 1L1 6l5 2 2 5z" fill="none" stroke="var(--green)" stroke-width="1.6"/></svg>Chatline</div>
    <div><svg width="13" height="13" viewBox="0 0 10 14"><path d="M5 0a5 5 0 0 0-5 5c0 4 5 9 5 9s5-5 5-9a5 5 0 0 0-5-5z" fill="var(--green)"/><circle cx="5" cy="5" r="2" fill="#fff"/></svg>United States</div>
  </div>
  <div class="abs pname">Lena Marsh</div>

  <div class="bar" style="top:342px">Details<b>+ Add</b></div>
  <div class="abs details">
    <div class="row" style="top:0"><span class="k">ID :</span><span class="v">41</span></div>
    <div class="row" style="top:28px"><span class="k">Email :</span><span class="v">lena.marsh@postmail.net</span><svg width="14" height="14" viewBox="0 0 14 14"><path d="M1 13l1-4 8-8 3 3-8 8z" fill="var(--cyan)"/></svg></div>
    <div class="row" style="top:55px"><span class="k">Phone :</span><span class="v">+1 (555) 204 7719</span><svg width="14" height="14" viewBox="0 0 14 14"><path d="M1 13l1-4 8-8 3 3-8 8z" fill="var(--cyan)"/></svg></div>
    <div class="row" style="top:82px"><span class="k">Address Line 1 :</span><span class="v">48 Alder Creek Lane</span><svg width="14" height="14" viewBox="0 0 14 14"><path d="M1 13l1-4 8-8 3 3-8 8z" fill="var(--cyan)"/></svg></div>
    <div class="row" style="top:110px"><span class="k">City :</span><span class="v">Fairview</span><svg width="14" height="14" viewBox="0 0 14 14"><path d="M1 13l1-4 8-8 3 3-8 8z" fill="var(--cyan)"/></svg></div>
    <div class="row" style="top:137px"><span class="k">State :</span><span class="v">North Carolina</span><svg width="14" height="14" viewBox="0 0 14 14"><path d="M1 13l1-4 8-8 3 3-8 8z" fill="var(--cyan)"/></svg></div>
  </div>
  <div class="abs show-all"><svg width="9" height="6" viewBox="0 0 9 6"><path d="M1 1l3.5 3.5L8 1" fill="none" stroke="#fff" stroke-width="1.5"/></svg>Show All</div>

  <div class="bar" style="top:650px">Tasks<b>+ Add</b></div>
  <div class="task" style="top:718px"><svg class="abs" style="top:3px" width="12" height="10" viewBox="0 0 12 10"><path d="M1 5l3 3 7-7" fill="none" stroke="var(--yellow)" stroke-width="2"/></svg><span class="t">Verify customer identity</span><span class="d">2017-15-01</span>
    <svg class="abs" style="left:369px;top:0" width="12" height="14" viewBox="0 0 12 14"><path d="M0 2h12M4 1h4M2 3h8l-1 11H3z" fill="none" stroke="var(--cyan)" stroke-width="1.8"/></svg></div>
  <div class="task" style="top:745px"><svg class="abs" style="top:1px" width="12" height="12" viewBox="0 0 12 12"><circle cx="6" cy="6" r="5" fill="none" stroke="var(--yellow)" stroke-width="1.5"/><path d="M6 3v3h2" fill="none" stroke="var(--yellow)" stroke-width="1.5"/></svg><span class="t">Check if the customer was billed twice</span><span class="d">2017-16-01</span>
    <svg class="abs" style="left:334px;top:3px" width="12" height="10" viewBox="0 0 12 10"><path d="M1 5l3 3 7-7" fill="none" stroke="var(--cyan)" stroke-width="2"/></svg>
    <svg class="abs" style="left:352px;top:3px" width="10" height="10" viewBox="0 0 10 10"><path d="M1 1l8 8M9 1l-8 8" stroke="var(--cyan)" stroke-width="2"/></svg>
    <svg class="abs" style="left:369px;top:-1px" width="12" height="14" viewBox="0 0 12 14"><path d="M0 2h12M4 1h4M2 3h8l-1 11H3z" fill="none" stroke="var(--cyan)" stroke-width="1.8"/></svg></div>

  <div class="bar" style="top:804px">Notes<b>+ Add</b></div>
  <div class="abs empty" style="top:865px">Empty</div>
</main>

<section class="abs chat">
  <svg class="abs" style="left:393px;top:22px" width="4" height="16" viewBox="0 0 4 16"><circle cx="2" cy="2" r="1.7" fill="#555"/><circle cx="2" cy="8" r="1.7" fill="#555"/><circle cx="2" cy="14" r="1.7" fill="#555"/></svg>

  <div class="avatar" style="left:29px;top:30px" role="img" aria-label="Customer photo"></div>
  <div class="bubble" style="left:112px;top:43px;width:89px;height:42px">Hello</div>
  <div class="bubble" style="left:111px;top:96px;width:238px;height:63px">Lorem Ipsum is simply dummy text of the printing</div>
  <div class="bubble" style="left:111px;top:181px;width:194px;height:42px">Lorem Ipsum is simply dummy</div>
  <div class="avatar" style="left:321px;top:167px" role="img" aria-label="Agent photo"></div>

  <div class="avatar" style="left:29px;top:236px" role="img" aria-label="Customer photo"></div>
  <div class="bubble" style="left:112px;top:248px;width:236px;height:43px">Lorem Ipsum is simply</div>
  <div class="bubble" style="left:111px;top:301px;width:238px;height:64px">Lorem Ipsum is simply dummy text of the printing</div>
  <div class="bubble" style="left:111px;top:385px;width:194px;height:43px">Lorem Ipsum is simply dummy</div>
  <div class="avatar" style="left:321px;top:373px" role="img" aria-label="Agent photo"></div>

  <div class="avatar" style="left:29px;top:450px" role="img" aria-label="Customer photo"></div>
  <div class="bubble" style="left:112px;top:462px;width:236px;height:43px">Lorem Ipsum is simply</div>
  <div class="bubble" style="left:111px;top:516px;width:238px;height:63px">Lorem Ipsum is simply dummy text of the printing</div>
  <div class="bubble" style="left:111px;top:600px;width:194px;height:42px">Lorem Ipsum is simply dummy</div>
  <div class="avatar" style="left:321px;top:587px" role="img" aria-label="Agent photo"></div>

  <svg class="abs" style="left:275px;top:808px" width="12" height="18" viewBox="0 0 12 18"><path d="M10 4C9 2 3 2 3 5s7 3 7 7-7 4-8 1M6 1v16" fill="none" stroke="#aaa" stroke-width="1.4"/></svg>
  <svg class="abs" style="left:303px;top:808px" width="18" height="18" viewBox="0 0 18 18"><path d="M15 8l-7 7a4 4 0 0 1-6-6l8-8a2.5 2.5 0 0 1 4 4l-8 8a1 1 0 0 1-2-2l7-7" fill="none" stroke="#aaa" stroke-width="1.4"/></svg>
  <svg class="abs" style="left:333px;top:809px" width="20" height="16" viewBox="0 0 20 16"><rect x="1" y="1" width="18" height="14" fill="none" stroke="#aaa" stroke-width="1.4"/><path d="M3 13l5-5 3 3 3-4 4 6z" fill="#aaa"/><circle cx="6" cy="5" r="1.5" fill="#aaa"/></svg>
  <svg class="abs" style="left:367px;top:807px" width="19" height="19" viewBox="0 0 19 19"><circle cx="9.5" cy="9.5" r="8.5" fill="none" stroke="#aaa" stroke-width="1.4"/><circle cx="6.5" cy="7.5" r="1" fill="#aaa"/><circle cx="12.5" cy="7.5" r="1" fill="#aaa"/><path d="M5.5 11.5c2 3 6 3 8 0" fill="none" stroke="#aaa" stroke-width="1.4"/></svg>
</section>
<div class="abs input-wrap"><div>Your Message...</div></div>

<footer class="abs footer">Copyrights 2017. Velorant. All rights reserved.</footer>
</body>
</html>
```